Consulting company requires a logo and business card design

I require a logo/business card design for a new company based in Sexsmith Alberta called TallMarsh Integrity Consulting Ltd. I plan to provide the following services: Construction management/inspection for the oil and gas industry, as well as general consulting for Asset Management, fleet management, etc. Have attached a copy of resume for use as guide for

Target Market(s)

Businesses within the oil and gas production, construction and shipping industry

Industry/Entity Type

Oil And Gas

Contact Information for Business Card

Believe should highlight, services offered, safety, quality,

Logo Text

TallMarsh Integrity Consulting (TMIC) ?

Font styles to use
Script

Requirements
Must have
• Open to all options

```html
<!DOCTYPE html>
<html lang="en">
<head>
<meta charset="utf-8">
<title>TallMarsh Integrity Consulting Ltd — Business Card</title>
<link href="https://fonts.googleapis.com/css2?family=Open+Sans:wght@400;600;700&display=swap" rel="stylesheet">
<style>
  :root {
    --brand-red: #c8193f;
    --paper: #ffffff;
    --ink: #2b2b2b;
    --blush: #f7e4e9;
    --backdrop: #ece9e4;
  }
  * { box-sizing: border-box; margin: 0; padding: 0; }
  html, body {
    width: 1200px; height: 900px; overflow: hidden;
    background: var(--backdrop);
    font-family: "Open Sans", sans-serif;
  }
  .canvas { position: relative; width: 1200px; height: 900px; }

  .card {
    position: absolute;
    width: 630px; height: 360px;
    border-radius: 4px;
    overflow: hidden;
    box-shadow: 0 10px 28px rgba(0,0,0,0.18);
  }

  /* Front */
  .card--front {
    left: 110px; top: 110px;
    background: var(--brand-red);
    color: var(--paper);
  }
  .front-brand {
    position: absolute; left: 0; right: 0; top: 96px;
    display: flex; justify-content: center; align-items: center; gap: 18px;
  }
  .brand-dot {
    width: 44px; height: 44px; border-radius: 50%;
    background: currentColor; flex: none;
  }
  .brand-name { font-weight: 400; line-height: 1.1; white-space: nowrap; }
  .brand-name__line1 { display: block; font-size: 34px; }
  .brand-name__line2 { display: block; font-size: 22px; letter-spacing: 0.34em; }
  .front-tagline {
    position: absolute; left: 50%; top: 222px; width: 470px;
    transform: translateX(-50%);
    text-align: center; font-weight: 700; font-size: 17px; line-height: 1.4;
  }

  /* Back */
  .card--back {
    left: 460px; top: 430px;
    background: var(--paper);
    color: var(--ink);
  }
  .back-decor {
    position: absolute; left: -20px; top: -40px;
    width: 340px; height: 340px; border-radius: 50%;
    background: var(--blush);
  }
  .contact {
    position: absolute; left: 360px; top: 32px;
    font-size: 13px; line-height: 1.4; color: var(--ink);
  }
  .contact__name { color: var(--brand-red); font-weight: 700; font-size: 19px; line-height: 1.15; }
  .contact__title { font-size: 13px; margin-bottom: 16px; }
  .contact__address { margin-bottom: 14px; }
  .contact__list { list-style: none; }
  .contact__list li { display: flex; align-items: center; gap: 10px; margin-bottom: 2px; }
  .contact__icon { width: 12px; height: 12px; fill: var(--brand-red); flex: none; }
  .back-brand {
    position: absolute; left: 40px; bottom: 44px;
    display: flex; align-items: center; gap: 14px;
    color: var(--brand-red);
  }
  .back-brand .brand-dot { width: 36px; height: 36px; }
  .back-brand .brand-name__line1 { font-size: 28px; }
  .back-brand .brand-name__line2 { font-size: 19px; }
</style>
</head>
<body>
<main class="canvas">

  <section class="card card--front" aria-label="Business card front">
    <div class="front-brand">
      <span class="brand-dot" aria-hidden="true"></span>
      <p class="brand-name">
        <span class="brand-name__line1">TallMarsh Integrity</span>
        <span class="brand-name__line2">Consulting Ltd</span>
      </p>
    </div>
    <p class="front-tagline">We are a construction management/inspection for the oil and gas industry, as well as general consulting for Asset Management, fleet management.</p>
  </section>

  <section class="card card--back" aria-label="Business card back">
    <div class="back-decor" aria-hidden="true"></div>

    <div class="contact">
      <p class="contact__name">Daniel Okafor</p>
      <p class="contact__title">Managing Director</p>
      <p class="contact__address">00000, Sample Street Here<br>Placeland, 000000.</p>
      <ul class="contact__list">
        <li>
          <svg class="contact__icon" viewBox="0 0 24 24" aria-hidden="true"><path d="M6.6 10.8a15.1 15.1 0 0 0 6.6 6.6l2.2-2.2a1 1 0 0 1 1-.25 11.4 11.4 0 0 0 3.6.57 1 1 0 0 1 1 1V20a1 1 0 0 1-1 1A17 17 0 0 1 3 4a1 1 0 0 1 1-1h3.5a1 1 0 0 1 1 1c0 1.25.2 2.45.57 3.57a1 1 0 0 1-.25 1z"/></svg>
          <span>000-555 010 000</span>
        </li>
        <li>
          <svg class="contact__icon" viewBox="0 0 24 24" aria-hidden="true"><path d="M2 5h20v14H2z"/><path d="M3 6l9 7 9-7" fill="none" stroke="#fff" stroke-width="2"/></svg>
          <span>info@example.com</span>
        </li>
        <li>
          <svg class="contact__icon" viewBox="0 0 24 24" aria-hidden="true"><path d="M10.6 13.4a1 1 0 0 1 0-1.4l3.5-3.5a3 3 0 1 1 4.2 4.2l-2 2-1.4-1.4 2-2a1 1 0 0 0-1.4-1.4L12 13.4a1 1 0 0 1-1.4 0zM13.4 10.6a1 1 0 0 1 0 1.4l-3.5 3.5a3 3 0 1 1-4.2-4.2l2-2 1.4 1.4-2 2a1 1 0 0 0 1.4 1.4L12 10.6a1 1 0 0 1 1.4 0z"/></svg>
          <span>www.example.com</span>
        </li>
      </ul>
    </div>

    <div class="back-brand">
      <span class="brand-dot" aria-hidden="true"></span>
      <p class="brand-name">
        <span class="brand-name__line1">TallMarsh Integrity</span>
        <span class="brand-name__line2">Consulting Ltd</span>
      </p>
    </div>
  </section>

</main>
</body>
</html>
```